Navoro & Omvar Automotive Repair Shop. Need a new website design.

We specialize in Navoro & Omvar auto repair, but also work on other Asian import vehicles. We have been in business for 7 years and pride ourselves on high quality auto repair that is fixed right the first time. Would like the automotive repair website to incorporate the colors black, red and white if possible and have our logo and some Navoro and Omvar vehicles included in the website.

Target Market(s)

Navoro & Omvar vehicle owners

Industry/Entity Type

Automotive Repair

Coding

Coded - Design and coding required

Number of Pages Required

5+ page

Colors
EB3D1F
EC4F4E
F09395
F8D3D4
FCEDEE

Requirements
Must have
• Home, Services, Contact Us, Schedule appointment, and a gallery tab that I can add shop pictures to when completed.
Nice to have
• Would like to see example pictures of job next to each service listed.
Should not have
• Service not related to auto repair. Ex. auto detailing, towing, car wash

```html
<!DOCTYPE html>
<html lang="en">
<head>
<meta charset="utf-8">
<title>Kestrel Automotive – Navoro &amp; Omvar Auto Repair</title>
<link rel="stylesheet" href="https://fonts.googleapis.com/css2?family=Syncopate:wght@700&family=Barlow:wght@400;500;600;700&display=swap">
<style>
:root{
  --red:#e3000f;
  --red-dark:#9a0008;
  --black:#0b0b0c;
  --ink:#1a1a1a;
  --grey:#555;
  --silver:#d9d9db;
  --white:#fff;
  --head:"Syncopate",sans-serif;
  --body:"Barlow",sans-serif;
}
*{box-sizing:border-box;margin:0;padding:0}
html,body{width:1200px;height:4762px;overflow:hidden}
body{position:relative;background:var(--white);font-family:var(--body);color:var(--ink)}
.abs{position:absolute}
.btn{position:absolute;display:flex;align-items:center;justify-content:center;background:linear-gradient(90deg,var(--red),var(--red-dark));color:var(--white);font:700 15px var(--body);text-transform:uppercase;letter-spacing:.3px}
.eyebrow{font:400 15px var(--head);color:var(--red);letter-spacing:1px;text-transform:uppercase}
.heading{font:700 32px var(--head);text-transform:uppercase;letter-spacing:1px}

/* hero */
.hero{position:absolute;left:0;top:0;width:1200px;height:760px;background:linear-gradient(110deg,#4a5559 0%,#2b3133 35%,#1a1a1c 60%,#3a3a3e 100%)}
.hero-photo{position:absolute;inset:0;background:linear-gradient(180deg,rgba(0,0,0,.75) 0%,rgba(0,0,0,.25) 45%,rgba(0,0,0,.1) 100%)}
.nav{position:absolute;top:68px;font:500 14px var(--body);color:var(--white);text-transform:uppercase}
.nav.active{border-bottom:2px solid var(--red);padding-bottom:4px}
.brand{position:absolute;left:514px;top:10px;width:172px;height:138px;background:var(--black);border:3px solid var(--red);display:flex;flex-direction:column;align-items:center;justify-content:center;gap:6px}
.brand .name{font:700 22px var(--head);color:var(--white)}
.brand .sub{font:700 12px var(--body);color:var(--red);text-transform:uppercase;letter-spacing:2px}
.nav-cta{position:absolute;left:917px;top:52px;width:200px;height:38px;border:1px solid var(--white);color:var(--white);font:600 11px var(--body);display:flex;align-items:center;justify-content:center;text-transform:uppercase}
.hero-frame{position:absolute;left:233px;top:240px;width:723px;height:162px;border:2px solid var(--white);border-top:none}
.hero-title{position:absolute;left:0;top:222px;width:1200px;text-align:center;font:700 29px var(--head);color:var(--white);text-transform:uppercase}
.hero-title span{background:#1e2022;padding:0 12px}
.hero-sub{position:absolute;left:0;top:260px;width:1200px;text-align:center;font:700 29px var(--head);color:var(--red);text-transform:uppercase}
.hero-text{position:absolute;left:320px;top:308px;width:560px;text-align:center;font:400 16px/23px var(--body);color:var(--white)}
.mouse{position:absolute;left:590px;top:592px}

/* about */
.about-photo{position:absolute;left:89px;top:869px;width:475px;height:422px}
.years{position:absolute;left:388px;top:1148px;width:115px;height:111px;background:linear-gradient(180deg,var(--red),var(--red-dark));color:var(--white);text-align:center;padding-top:14px}
.years b{display:block;font:700 34px var(--head)}
.years span{font:600 14px/16px var(--body);text-transform:uppercase}
.about-copy{position:absolute;left:614px;top:958px;width:514px}
.about-copy .lead{font:600 16px/23px var(--body);color:var(--ink);margin-bottom:14px}
.about-copy p{font:400 14px/23px var(--body);color:var(--grey)}
.outline-btn{position:absolute;left:617px;top:1239px;width:165px;height:44px;border:2px solid var(--red);color:var(--red);font:600 14px var(--body);display:flex;align-items:center;justify-content:center;letter-spacing:1px}

/* services */
.dark{position:absolute;left:0;top:1562px;width:1200px;height:740px;background:radial-gradient(ellipse at 50% 40%,#1c1c1e,#050505)}
.partners{position:absolute;left:111px;top:1383px;width:958px;height:255px;background:var(--white);box-shadow:0 4px 20px rgba(0,0,0,.15)}
.corner-tl{position:absolute;left:103px;top:1375px;width:96px;height:56px;border-left:6px solid var(--red);border-top:6px solid var(--red)}
.corner-br{position:absolute;left:980px;top:1585px;width:96px;height:57px;border-right:6px solid var(--red);border-bottom:6px solid var(--red)}
.partners h3{position:absolute;left:0;top:36px;width:958px;text-align:center;font:700 17px/25px var(--head);text-transform:uppercase}
.badge{position:absolute;top:100px}
.partner-name{position:absolute;top:130px;font:700 22px var(--body);color:var(--red);text-transform:uppercase}
.svc-title{position:absolute;left:0;width:1200px;text-align:center}
.svc{position:absolute;display:flex;gap:14px;color:var(--white);font:500 15px/22px var(--body)}
.svc svg{flex:none}

/* gallery */
.gallery-bg{position:absolute;left:0;top:2293px;width:1200px;height:1003px;background:linear-gradient(180deg,#c7c7c9 0%,#f1f1f2 40%,#e3e3e5 75%,#bfbfc1 100%)}
.engine{position:absolute;left:431px;top:2237px;width:368px;height:278px;border-radius:40px;background:radial-gradient(circle,#e9e9ea,#9c9c9e 60%,#4a4a4d)}
.photo{position:absolute}

/* makes */
.makes-title{position:absolute;left:0;top:3356px;width:1200px;text-align:center;font:700 20px/25px var(--head);text-transform:uppercase}
.makes{position:absolute;left:135px;top:3483px;width:921px;height:287px;display:grid;grid-template-columns:repeat(4,1fr);grid-template-rows:repeat(2,1fr);border:1px solid #cfcfd2}
.make{border:1px solid #cfcfd2;display:flex;align-items:center;justify-content:center;font:700 22px var(--body);letter-spacing:2px;text-transform:uppercase;color:var(--ink)}
.make.hover{background:linear-gradient(180deg,#eee,#b9b9bc)}

/* contact */
.contact{position:absolute;left:0;top:3857px;width:1200px;height:700px;background:linear-gradient(160deg,#161618,#050505 60%,#222)}
.contact-car{position:absolute;left:0;top:4240px;width:560px;height:300px;background:radial-gradient(ellipse at 40% 60%,#3b3b3e,#0b0b0c 70%)}
.contact-copy{position:absolute;left:135px;top:4121px;width:400px;font:400 16px/27px var(--body);color:var(--white)}
.form{position:absolute;left:594px;top:3963px;width:491px;height:419px;background:linear-gradient(135deg,var(--red),#b0000a)}
.form h4{position:absolute;left:43px;top:40px;font:700 17px var(--head);color:var(--white);text-transform:uppercase}
.field{position:absolute;border:1px solid rgba(255,255,255,.8);color:var(--white);font:500 10px var(--body);padding:9px 10px}
.submit{position:absolute;left:44px;top:275px;width:131px;height:35px;background:var(--black);color:var(--white);font:700 12px var(--head);display:flex;align-items:center;justify-content:center}

/* footer */
.footer-nav{position:absolute;top:4606px;left:0;width:1200px;display:flex;justify-content:center;gap:58px;font:600 17px var(--body);text-transform:uppercase}
.footer-nav li{list-style:none;position:relative}
.footer-nav li+li::before{content:"";position:absolute;left:-32px;top:9px;width:6px;height:6px;background:var(--red)}
.copy{position:absolute;top:4657px;left:0;width:1200px;text-align:center;font:400 13px var(--body)}
.social{position:absolute;top:4703px;left:0;width:1200px;display:flex;justify-content:center;gap:20px;font:600 13px var(--body)}
.social span{display:flex;align-items:center;gap:5px}
.social i{width:10px;height:10px;border-radius:50%;background:var(--red);display:block}
</style>
</head>
<body>

<!-- HERO -->
<section class="hero">
  <div class="hero-photo" role="img" aria-label="Workshop photo with a silver sedan on the left and an opened engine on the right"></div>
  <a class="nav active" style="left:162px">Home</a>
  <a class="nav" style="left:246px">About Us</a>
  <a class="nav" style="left:356px">Our Services</a>
  <a class="nav" style="left:722px">Gallery</a>
  <a class="nav" style="left:831px">Contact</a>
  <div class="nav-cta">Schedule an appointment</div>
  <div class="brand"><span class="name">Kestrel</span><span class="sub">Automotive</span></div>
  <div class="hero-frame"></div>
  <h1 class="hero-title"><span>Locally owned auto repair</span></h1>
  <div class="hero-sub">Shop in Harlow Springs</div>
  <p class="hero-text">Kestrel Automotive is a locally owned and operated auto repair shop in Harlow Springs that offers comprehensive car care and services</p>
  <div class="btn" style="left:475px;top:379px;width:263px;height:48px">Schedule an appointment</div>
  <svg class="mouse" width="20" height="48" viewBox="0 0 20 48"><rect x="2" y="1" width="16" height="26" rx="8" fill="none" stroke="#fff" stroke-width="2"/><line x1="10" y1="7" x2="10" y2="12" stroke="#fff" stroke-width="2"/><path d="M5 33l5 5 5-5M5 40l5 5 5-5" fill="none" stroke="#fff" stroke-width="1.5"/></svg>
</section>
<svg class="abs" style="left:0;top:580px" width="1200" height="200" viewBox="0 0 1200 200">
  <polygon points="0,180 1200,80 1200,200 0,200" fill="#fff"/>
  <polygon points="600,140 1200,20 1200,80 0,180 0,178" fill="#e3000f"/>
  <polygon points="0,178 600,140 0,175" fill="#e3000f"/>
</svg>

<!-- ABOUT -->
<svg class="about-photo" viewBox="0 0 475 422" role="img" aria-label="Technician working underneath a lifted vehicle">
  <defs><linearGradient id="aboutG" x1="0" y1="0" x2="0" y2="1"><stop offset="0" stop-color="#8a8a8c"/><stop offset="1" stop-color="#2a2a2c"/></linearGradient></defs>
  <polygon points="70,30 237,0 405,30 430,80 430,250 237,422 45,250 45,80" fill="#fff" stroke="#1a1a1a" stroke-width="3"/>
  <polygon points="80,40 237,12 395,40 415,85 415,245 237,405 60,245 60,85" fill="url(#aboutG)"/>
</svg>
<div class="years"><b>20</b><span>Years of<br>experience</span></div>
<div class="eyebrow abs" style="left:608px;top:861px">Our company</div>
<h2 class="heading abs" style="left:608px;top:884px">About Kestrel</h2>
<div class="abs" style="left:968px;top:897px;width:8px;height:8px;background:var(--red)"></div>
<div class="abs" style="left:976px;top:900px;width:224px;height:1px;background:#e8a0a0"></div>
<div class="about-copy">
  <p class="lead">Kestrel Automotive is a locally owned and operated auto repair shop in Harlow Springs that offers comprehensive car care and services for Navoro &amp; Omvar and all other Asian imports vehicles.</p>
  <p>Led by an NTC master certified technician with 20 years experience working for Navoro &amp; Omvar dealerships, our auto shop is your go to facility for everything from factory auto maintenance, including oil changes, fluid services and tune ups, to complex engine repairs, hybrid diagnostic &amp; repair, brake jobs, etc. We have state of the art equipment and tools to ensure that we can properly diagnose and repair your vehicle to get you back on the road quickly. Our work comes with a warranty and we offer towing if needed. We also offer discounts for RideGo &amp; Hoply drivers.</p>
</div>
<div class="outline-btn">LEARN MORE</div>

<!-- SERVICES -->
<section class="dark"></section>
<div class="corner-tl"></div>
<div class="corner-br"></div>
<div class="partners">
  <h3>Authorized installer for Veltrax oil,<br>Corvane battery</h3>
  <svg class="badge" style="left:119px" width="84" height="114" viewBox="0 0 84 114"><rect x="1" y="1" width="82" height="112" rx="4" fill="#fff" stroke="#1a3c8c" stroke-width="2"/><circle cx="42" cy="40" r="26" fill="#1a5fbf"/></svg>
  <svg class="badge" style="left:300px;top:104px" width="104" height="104" viewBox="0 0 104 104"><circle cx="52" cy="52" r="48" fill="none" stroke="#2aa3c9" stroke-width="3"/><circle cx="52" cy="52" r="34" fill="#e7f5fa"/></svg>
  <span class="partner-name" style="left:440px">Corvane</span>
  <span class="partner-name" style="left:700px">Veltrax</span>
</div>
<div class="abs" style="left:599px;top:1646px;width:2px;height:54px;background:var(--red)"></div>
<div class="abs" style="left:594px;top:1698px;width:10px;height:10px;background:var(--red)"></div>
<div class="svc-title eyebrow" style="top:1726px">What we do</div>
<h2 class="svc-title heading" style="top:1750px;color:var(--white);font-size:29px">Services provide</h2>

<svg width="0" height="0" style="position:absolute"><symbol id="ic" viewBox="0 0 34 34"><circle cx="17" cy="17" r="13" fill="none" stroke="#e3000f" stroke-width="2.5"/><path d="M11 23l8-8m-2-4l6 6" stroke="#e3000f" stroke-width="2.5" stroke-linecap="round"/></symbol></svg>

<div class="svc" style="left:120px;top:1826px"><svg width="34" height="34"><use href="#ic"/></svg>Oil Changes</div>
<div class="svc" style="left:120px;top:1872px"><svg width="34" height="34"><use href="#ic"/></svg>Computer Diagnostics</div>
<div class="svc" style="left:120px;top:1918px"><svg width="34" height="34"><use href="#ic"/></svg>Electrical Specialists</div>
<div class="svc" style="left:120px;top:1965px"><svg width="34" height="34"><use href="#ic"/></svg>Tires</div>
<div class="svc" style="left:120px;top:2011px"><svg width="34" height="34"><use href="#ic"/></svg>Tire Balance &amp; Rotations</div>
<div class="svc" style="left:120px;top:2057px"><svg width="34" height="34"><use href="#ic"/></svg>Pre Purchase Inspections</div>
<div class="svc" style="left:120px;top:2103px"><svg width="34" height="34"><use href="#ic"/></svg>Insurance Claims</div>
<div class="svc" style="left:120px;top:2149px"><svg width="34" height="34"><use href="#ic"/></svg>Emission Repair &amp; Catalytic<br>Converters</div>

<div class="svc" style="left:429px;top:1826px"><svg width="34" height="34"><use href="#ic"/></svg>Engine Repair</div>
<div class="svc" style="left:429px;top:1872px"><svg width="34" height="34"><use href="#ic"/></svg>Heating &amp; AC Repair</div>
<div class="svc" style="left:429px;top:1918px"><svg width="34" height="34"><use href="#ic"/></svg>State Inspection</div>
<div class="svc" style="left:429px;top:1965px"><svg width="34" height="34"><use href="#ic"/></svg>Suspension Service &amp; Repair</div>
<div class="svc" style="left:429px;top:2011px"><svg width="34" height="34"><use href="#ic"/></svg>Leveling Kits &amp; Minor Lift Kit installation</div>
<div class="svc" style="left:429px;top:2057px"><svg width="34" height="34"><use href="#ic"/></svg>Brakes Service &amp; Repair</div>
<div class="svc" style="left:429px;top:2103px"><svg width="34" height="34"><use href="#ic"/></svg>Exhaust, Muffler Service &amp; Repair</div>
<div class="svc" style="left:429px;top:2149px"><svg width="34" height="34"><use href="#ic"/></svg>Automatic, Manual, Computerized<br>Transmission Service &amp; Repair</div>

<div class="svc" style="left:786px;top:1826px"><svg width="34" height="34"><use href="#ic"/></svg>Clutch Service &amp; Repair</div>
<div class="svc" style="left:786px;top:1872px"><svg width="34" height="34"><use href="#ic"/></svg>CV Axle Service &amp; Repair</div>
<div class="svc" style="left:786px;top:1918px"><svg width="34" height="34"><use href="#ic"/></svg>Fuel Injection System Service<br>Cleaning &amp; Repair</div>
<div class="svc" style="left:786px;top:1987px"><svg width="34" height="34"><use href="#ic"/></svg>Timing Belts &amp; Water Pumps</div>
<div class="svc" style="left:786px;top:2033px"><svg width="34" height="34"><use href="#ic"/></svg>Radiators &amp; Fans Service &amp; Repair</div>
<div class="svc" style="left:786px;top:2080px"><svg width="34" height="34"><use href="#ic"/></svg>Tune ups &amp; Factory Scheduled<br>Maintenance</div>
<div class="svc" style="left:786px;top:2149px"><svg width="34" height="34"><use href="#ic"/></svg>Hybrid Vehicle diagnostic &amp; repair<br>24-hr Night Drop</div>

<!-- GALLERY -->
<section class="gallery-bg"></section>
<svg class="abs" style="left:0;top:2293px" width="1200" height="120" viewBox="0 0 1200 120"><polygon points="0,0 1200,0 1200,20 780,110 420,110 0,20" fill="#050505"/></svg>
<div class="engine" role="img" aria-label="Chrome V8 engine render"></div>
<div class="svc-title eyebrow" style="top:2545px">Photo gallery</div>
<h2 class="svc-title heading" style="top:2569px;font-size:30px">Our gallery</h2>
<div class="photo" style="left:115px;top:2646px;width:323px;height:235px;background:linear-gradient(135deg,#6b6357,#2c2a27)" role="img" aria-label="Mechanic's hands working on a suspension"></div>
<div class="photo" style="left:451px;top:2646px;width:322px;height:235px;background:linear-gradient(135deg,#3a3a3c,#8e8e90)" role="img" aria-label="Front of a dark Omvar SUV in the shop"></div>
<div class="photo" style="left:786px;top:2646px;width:323px;height:235px;background:linear-gradient(135deg,#5a6068,#1f2328)" role="img" aria-label="Engine bay with the engine partly disassembled"></div>
<div class="photo" style="left:118px;top:2899px;width:488px;height:237px;background:linear-gradient(135deg,#c9cacd,#6c6f75)" role="img" aria-label="Silver Navoro pickup raised on a lift"></div>
<div class="photo" style="left:621px;top:2899px;width:488px;height:237px;background:linear-gradient(180deg,#9bb3cc,#8a7a62 55%,#4a4a4a)" role="img" aria-label="Row of Navoro SUVs parked in front of the shop"></div>
<div class="btn" style="left:466px;top:3180px;width:290px;height:56px">Schedule an appointment</div>

<!-- MAKES -->
<h2 class="makes-title">Kestrel Automotive specializes in Navoro &amp; Omvar<br>auto repair but also service and repair<br>the following makes</h2>
<div class="makes">
  <div class="make" style="color:#1d3f8f">Arvela</div>
  <div class="make hover">Hanvik</div>
  <div class="make" style="font-weight:500;letter-spacing:6px">Inverra</div>
  <div class="make" style="font-size:30px">Kado</div>
  <div class="make" style="font-size:16px">Mirasho</div>
  <div class="make" style="color:#666">Mazeno</div>
  <div class="make" style="font-weight:500;letter-spacing:4px">Nerano</div>
  <div class="make" style="color:var(--red)">Hoshiro</div>
</div>

<!-- CONTACT -->
<section class="contact"></section>
<div class="contact-car" role="img" aria-label="Front of a dark Omvar SUV"></div>
<div class="eyebrow abs" style="left:135px;top:4023px">Get in touch</div>
<div class="abs" style="left:101px;top:4063px;width:8px;height:8px;background:var(--red)"></div>
<h2 class="heading abs" style="left:135px;top:4050px;color:var(--white);font-size:33px">Contact <span style="color:var(--red)">us</span></h2>
<p class="contact-copy">Contact us for a free estimate! Please include year, make, and model and the service or repair you would like repair you would like an estimate on.</p>
<div class="btn" style="left:139px;top:4212px;width:236px;height:44px;font-size:13px">Schedule an appointment</div>
<div class="form">
  <h4>Leave us a message</h4>
  <div class="field" style="left:42px;top:79px;width:200px;height:35px">First Name*</div>
  <div class="field" style="left:251px;top:79px;width:203px;height:35px">Last Name*</div>
  <div class="field" style="left:42px;top:129px;width:200px;height:35px">Email address*</div>
  <div class="field" style="left:251px;top:129px;width:203px;height:35px">Phone*</div>
  <div class="field" style="left:42px;top:179px;width:412px;height:79px">Message</div>
  <div class="submit">SUBMIT</div>
</div>

<!-- FOOTER -->
<svg class="abs" style="left:0;top:4430px" width="1200" height="150" viewBox="0 0 1200 150">
  <polygon points="0,0 1200,130 1200,150 0,150" fill="#fff"/>
  <polygon points="0,30 600,70 0,110" fill="#e3000f"/>
  <polygon points="600,70 1200,95 1200,130 0,115 0,110" fill="#fff"/>
</svg>
<div class="brand" style="top:4420px;left:509px;width:182px;height:140px"><span class="name">Kestrel</span><span class="sub">Automotive</span></div>
<ul class="footer-nav"><li>Home</li><li>About Us</li><li>Our Services</li><li>Gallery</li><li>Contact</li></ul>
<p class="copy">Copyright © 2024 Kestrel Automotive. All rights reserved.</p>
<div class="social"><span><i></i>Friendly</span><span><i></i>Chirp</span><span><i></i>Linkpro</span><span><i></i>Snapgram</span></div>

</body>
</html>
```